Thornvale Group needs a business card design

We need a new business card design using the logo recently selected in a logo competition on Pixel Bazaar. Our business is a consultancy specializing in aviation and energy and the winning business card design will promote an image of precision and professionalism with creativity.

Please use the logo with the name on the front of the card and use a complementary font. Make the back white with either the light grey or dark grey logo.

Target Market(s)

Senior finance and legal leaders at aviation and energy companies

Industry/Entity Type

Management Consulting

Contact Information for Business Card

Peter Castrell
President
Thornvale Group

www.thornvalegroup.example

(555) 204-6391
pc@thornvalegroup.example

Requirements
Must have
• Professional font that goes well with the logo font

```html
<!DOCTYPE html>
<html lang="en">
<head>
<meta charset="utf-8">
<title>Thornvale Group – Business Card</title>
<link rel="stylesheet" href="https://fonts.googleapis.com/css2?family=Montserrat:wght@400&family=Open+Sans:wght@400;700&display=swap">
<style>
  :root {
    --backdrop: #e9e6e1;
    --card-white: #ffffff;
    --navy: #1d4a78;
    --steel-blue: #2f6d98;
    --slate-grey: #7d8287;
    --text-grey: #6c7075;
    --back-top: #eceef6;
    --back-bottom: #b4b9d3;
    --shadow: rgba(40, 30, 20, 0.22);
  }
  * { box-sizing: border-box; margin: 0; padding: 0; }
  html, body {
    width: 1200px;
    height: 913px;
    overflow: hidden;
    background: var(--backdrop);
  }
  .canvas {
    position: relative;
    width: 1200px;
    height: 913px;
  }
  .card {
    position: absolute;
    width: 560px;
    height: 320px;
    border-radius: 3px;
    box-shadow: 0 10px 28px var(--shadow);
    overflow: hidden;
  }

  /* Front */
  .card--front {
    left: 50px;
    top: 130px;
    background: var(--card-white);
  }
  .front-accent {
    position: absolute;
    right: 0;
    top: 0;
    width: 200px;
    height: 100%;
    display: flex;
  }
  .front-accent__blue { flex: 1; background: linear-gradient(180deg, var(--steel-blue), var(--navy)); }
  .front-accent__grey { flex: 1; background: linear-gradient(180deg, #8c9196, #5f6469); }
  .front-content {
    position: absolute;
    left: 40px;
    top: 44px;
  }
  .wordmark {
    display: flex;
    align-items: center;
    gap: 10px;
    font-family: 'Montserrat', sans-serif;
    font-weight: 400;
    color: var(--navy);
    letter-spacing: 0.12em;
    text-transform: uppercase;
  }
  .wordmark__square {
    width: 18px;
    height: 18px;
    background: var(--navy);
  }
  .wordmark--front { font-size: 22px; }
  .person { margin-top: 56px; }
  .person__name {
    font-family: 'Open Sans', sans-serif;
    font-weight: 700;
    font-size: 21px;
    color: var(--navy);
  }
  .person__title {
    font-family: 'Open Sans', sans-serif;
    font-size: 13px;
    color: var(--text-grey);
    margin-top: 2px;
  }
  .contact {
    list-style: none;
    margin-top: 20px;
    font-family: 'Open Sans', sans-serif;
    font-size: 13px;
    color: var(--navy);
  }
  .contact__item {
    display: flex;
    align-items: center;
    gap: 8px;
    line-height: 20px;
  }
  .contact__icon { width: 11px; height: 11px; flex: none; }

  /* Back */
  .card--back {
    left: 600px;
    top: 450px;
    background: linear-gradient(165deg, var(--back-top), var(--back-bottom));
    display: flex;
    align-items: center;
    justify-content: center;
  }
  .wordmark--back { font-size: 28px; }
</style>
</head>
<body>
<main class="canvas">

  <section class="card card--front" aria-label="Business card front">
    <div class="front-accent" aria-hidden="true">
      <div class="front-accent__blue"></div>
      <div class="front-accent__grey"></div>
    </div>
    <div class="front-content">
      <div class="wordmark wordmark--front">
        <span class="wordmark__square"></span>
        <span>Thornvale Group</span>
      </div>
      <div class="person">
        <h1 class="person__name">Peter Castrell</h1>
        <p class="person__title">President</p>
      </div>
      <ul class="contact">
        <li class="contact__item">
          <svg class="contact__icon" viewBox="0 0 12 12" aria-hidden="true"><path d="M2.5 1 L4.5 1 L5.2 3.6 L4 4.6 C4.7 6 6 7.3 7.4 8 L8.4 6.8 L11 7.5 L11 9.5 C11 10.3 10.3 11 9.5 11 C5 11 1 7 1 2.5 C1 1.7 1.7 1 2.5 1 Z" fill="var(--text-grey)"/></svg>
          <span>(555) 204-6391</span>
        </li>
        <li class="contact__item">
          <svg class="contact__icon" viewBox="0 0 12 12" aria-hidden="true"><rect x="1" y="2.5" width="10" height="7" fill="none" stroke="var(--text-grey)" stroke-width="1.2"/><path d="M1 2.5 L6 6.5 L11 2.5" fill="none" stroke="var(--text-grey)" stroke-width="1.2"/></svg>
          <span>pc@thornvalegroup.example</span>
        </li>
        <li class="contact__item">
          <svg class="contact__icon" viewBox="0 0 12 12" aria-hidden="true"><circle cx="6" cy="6" r="5" fill="none" stroke="var(--text-grey)" stroke-width="1.2"/><ellipse cx="6" cy="6" rx="2.2" ry="5" fill="none" stroke="var(--text-grey)" stroke-width="1"/><path d="M1 6 H11" stroke="var(--text-grey)" stroke-width="1"/></svg>
          <span>www.thornvalegroup.example</span>
        </li>
      </ul>
    </div>
  </section>

  <section class="card card--back" aria-label="Business card back">
    <div class="wordmark wordmark--back">
      <span>Thornvale Group</span>
    </div>
  </section>

</main>
</body>
</html>
```